Marwick Law Letterhead

We need a new letterhead design for a Law Firm. The address for the law firm is 1475 Calloway Street, Suite 210, Houston, Texas 77041. Phone Number: 832-361-9027; Fax Number: 832-614-7359. The logo is uploaded to the project.

```html
<!DOCTYPE html>
<html lang="en">
<head>
<meta charset="utf-8">
<title>Marwick Law Letterhead</title>
<link href="https://fonts.googleapis.com/css2?family=Outfit:wght@400;700&display=swap" rel="stylesheet">
<style>
:root{
  --navy:#1c2d5a;
  --red:#c8102e;
  --red-dark:#8e0f1f;
  --ink:#2a2a2a;
  --rule:#555;
  --backdrop:#ffffff;
  --paper:#ffffff;
}
*{margin:0;padding:0;box-sizing:border-box}
html,body{width:1200px;height:2859px;overflow:hidden;background:var(--backdrop)}
body{font-family:'Outfit',sans-serif;color:var(--ink);position:relative}
.letterhead{position:absolute;left:60px;top:667px;width:1080px;height:1525px;background:var(--paper);box-shadow:0 4px 28px rgba(0,0,0,.22);overflow:hidden}
.brand{position:absolute;left:83px;top:72px;display:flex;align-items:center;gap:16px}
.brand-dot{width:64px;height:64px;border-radius:50%;background:var(--navy)}
.brand-name{font-size:44px;font-weight:400;color:var(--navy);letter-spacing:.5px}
.salutation{position:absolute;left:74px;top:250px;font-size:25px}
.letter-body{position:absolute;left:74px;top:291px;width:916px;font-size:17.6px;line-height:22px;text-align:justify}
.letter-body p{margin-bottom:22px}
.sign-line{position:absolute;left:74px;top:1137px;width:400px;border-top:2px dashed var(--ink)}
.signature{position:absolute;left:74px;top:1152px}
.person-name{font-weight:700;color:var(--navy);font-size:27px;line-height:34px}
.person-title{font-size:27px;line-height:34px}
.footer-rule{position:absolute;left:74px;top:1316px;width:936px;border-top:1.5px solid var(--rule)}
.footer-sign{position:absolute;left:74px;top:1372px}
.contact{position:absolute;font-size:19.5px;line-height:27px}
.contact li{list-style:none;display:flex;align-items:center;gap:16px}
.contact svg{width:18px;height:18px;flex:none}
.contact-phone{left:368px;top:1376px}
.contact-phone li:not(:last-child){font-weight:700;color:var(--navy)}
.contact-place{left:690px;top:1370px}
.contact-place li{align-items:flex-start}
.contact-place svg{margin-top:5px}
.footer-band{position:absolute;left:0;bottom:0;width:1080px;height:40px}
</style>
</head>
<body>
<main class="letterhead">
  <header class="brand">
    <span class="brand-dot"></span>
    <span class="brand-name">Marwick Law</span>
  </header>

  <p class="salutation">Dear Sir,</p>

  <section class="letter-body">
    <p>Quis ipsum suspendisse ultrices gravida. Risus commodo viverra maecenas accumsan lacus vel facilisis. Lorem ipsum dolor sit amet, consectetur adipiscing elit, sed do eiusmod tempor incididunt ut labore et dolore magna aliqua. Quis ipsum suspendisse ultrices gravida. Risus commodo viverra maecenas accumsan lacus vel facilisis. Lorem ipsum dolor sit amet, consectetur adipiscing elit, sed do eiusmod tempor incididunt ut labore et dolore magna aliqua. Quis ipsum suspendisse ultrices gravida. Risus commodo viverra maecenas accumsan lacus vel facilisis. Lorem ipsum dolor sit amet, consectetur adipiscing elit, sed do eiusmod tempor incididunt ut labore et dolore magna aliqua. Quis ipsum suspendisse ultrices gravida. Risus commodo viverra maecenas accumsan lacus vel facilisis.</p>
    <p>Lorem ipsum dolor sit amet, consectetur adipiscing elit, sed do eiusmod tempor incididunt ut labore et dolore magna aliqua. Quis ipsum suspendisse ultrices gravida. Risus commodo viverra maecenas accumsan lacus vel facilisis. Lorem ipsum dolor sit amet, consectetur adipiscing elit, sed do eiusmod tempor incididunt ut labore et dolore magna aliqua. Quis ipsum suspendisse ultrices gravida. Risus commodo viverra maecenas accumsan lacus vel facilisis. Lorem ipsum dolor sit amet, consectetur adipiscing elit, sed do eiusmod tempor incididunt ut labore et dolore magna aliqua. Quis ipsum suspendisse ultrices gravida. Risus commodo viverra maecenas accumsan lacus vel facilisis. Lorem ipsum dolor sit amet, consectetur adipiscing elit, sed do eiusmod tempor incididunt ut labore et dolore magna aliqua. Quis ipsum suspendisse ultrices gravida. Risus commodo viverra maecenas accumsan lacus vel facilisis.</p>
    <p>Lorem ipsum dolor sit amet, consectetur adipiscing elit, sed do eiusmod tempor incididunt ut labore et dolore magna aliqua. Quis ipsum suspendisse ultrices gravida. Risus commodo viverra maecenas accumsan lacus vel facilisis. Lorem ipsum dolor sit amet, consectetur adipiscing elit, sed do eiusmod tempor incididunt ut labore et dolore magna aliqua. Quis ipsum suspendisse ultrices gravida. Risus commodo viverra maecenas accumsan lacus vel facilisis. Lorem ipsum dolor sit amet, consectetur adipiscing elit, sed do eiusmod tempor incididunt ut labore et dolore magna aliqua. Quis ipsum suspendisse ultrices gravida. Risus commodo viverra maecenas accumsan lacus vel facilisis. Lorem ipsum dolor sit amet, consectetur adipiscing elit, sed do eiusmod tempor incididunt ut labore et dolore magna aliqua. Quis ipsum suspendisse ultrices gravida. Risus commodo viverra maecenas accumsan lacus vel facilisis. Lorem ipsum dolor sit amet, consectetur adipiscing elit, sed do eiusmod tempor incididunt ut labore et dolore magna aliqua. Quis ipsum suspendisse ultrices gravida. Risus commodo viverra maecenas accumsan lacus vel facilisis. Lorem ipsum dolor sit amet, consectetur adipiscing elit, sed do eiusmod tempor incididunt ut labore et dolore magna aliqua. Quis ipsum suspendisse ultrices gravida. Risus commodo viverra maecenas accumsan lacus vel facilisis.</p>
  </section>

  <div class="sign-line"></div>
  <div class="signature">
    <div class="person-name">Daniel R. Marwick</div>
    <div class="person-title">Attorney at Law</div>
  </div>

  <div class="footer-rule"></div>
  <div class="footer-sign">
    <div class="person-name">Daniel R. Marwick</div>
    <div class="person-title">Attorney at Law</div>
  </div>

  <ul class="contact contact-phone">
    <li><svg viewBox="0 0 24 24"><path fill="var(--red)" d="M6.6 10.8a15.1 15.1 0 0 0 6.6 6.6l2.2-2.2c.3-.3.7-.4 1-.2 1.1.4 2.3.6 3.6.6.6 0 1 .4 1 1V20c0 .6-.4 1-1 1A17 17 0 0 1 3 4c0-.6.4-1 1-1h3.5c.6 0 1 .4 1 1 0 1.3.2 2.5.6 3.6.1.3 0 .7-.2 1z"/></svg>832-361-9027</li>
    <li><svg viewBox="0 0 24 24"><path fill="var(--red)" d="M6 2h12v5H6zM4 8h16a2 2 0 0 1 2 2v7h-4v5H6v-5H2v-7a2 2 0 0 1 2-2zm4 8v4h8v-4z"/></svg>832-614-7359</li>
    <li><svg viewBox="0 0 24 24"><path fill="var(--red)" d="M3 5h18v14H3zm2 2v.5l7 5 7-5V7z"/></svg>contact@marwickinjury.co</li>
  </ul>

  <ul class="contact contact-place">
    <li><svg viewBox="0 0 24 24"><path fill="var(--red)" d="M12 2a7 7 0 0 0-7 7c0 5 7 13 7 13s7-8 7-13a7 7 0 0 0-7-7zm0 9.5A2.5 2.5 0 1 1 12 6.5a2.5 2.5 0 0 1 0 5z"/></svg><span>1475 Calloway Street, Suite<br>210, Houston, Texas 77041</span></li>
    <li><svg viewBox="0 0 24 24"><circle cx="12" cy="12" r="9" fill="none" stroke="var(--red)" stroke-width="2"/><path d="M3 12h18M12 3c3 3 3 15 0 18M12 3c-3 3-3 15 0 18" fill="none" stroke="var(--red)" stroke-width="1.6"/></svg>www.marwickinjury.com</li>
  </ul>

  <svg class="footer-band" viewBox="0 0 1080 40" preserveAspectRatio="none">
    <defs>
      <linearGradient id="bandRed" x1="0" x2="1">
        <stop offset="0" stop-color="var(--red-dark)"/>
        <stop offset="1" stop-color="var(--red)"/>
      </linearGradient>
    </defs>
    <polygon points="0,28 772,28 766,40 0,40" fill="var(--navy)"/>
    <polygon points="790,0 1080,0 1080,40 770,40" fill="url(#bandRed)"/>
  </svg>
</main>
</body>
</html>
```